Business Card & Letterhead Design

We a financial advice company based in Australia. We provide advice to wealthy farmers.

We are changing our business name FROM Brightvale Financial TO Tallowmere Wealth and we need a new letterhead and double sided business card design

Attached is designs from our previous branding (Brightvale Financial) as it includes all the details we require on the new Tallowmere Wealth business cards and letterhead.

Need extra days to review

```html
<!DOCTYPE html>
<html lang="en">
<head>
<meta charset="utf-8">
<title>Tallowmere Wealth – Letterhead &amp; Business Card</title>
<link rel="stylesheet" href="https://fonts.googleapis.com/css2?family=Open+Sans:ital,wght@0,400;0,600;0,700;1,600&display=swap">
<style>
  :root{
    --bg:#e4e6e8;
    --paper:#f4f5f5;
    --charcoal:#3b3f43;
    --charcoal-dark:#2c2f32;
    --charcoal-light:#55595d;
    --ink:#2a2c2e;
    --muted:#6d7175;
    --on-dark:#e6e8ea;
    --on-dark-muted:#b3b7bb;
    --accent:#7f8a93;
  }
  *{box-sizing:border-box;margin:0;padding:0}
  html,body{width:1200px;height:738px;overflow:hidden;background:var(--bg);font-family:"Open Sans",Arial,sans-serif;color:var(--ink)}
  .canvas{position:relative;width:1200px;height:738px}

  /* Letterhead */
  .letterhead{position:absolute;left:40px;top:18px;width:495px;height:702px;background:var(--paper);box-shadow:0 2px 10px rgba(0,0,0,.18);overflow:hidden}
  .lh-sidebar{position:absolute;left:0;top:0;width:138px;height:680px;background:linear-gradient(180deg,var(--charcoal-dark),var(--charcoal) 55%,var(--charcoal-light));color:var(--on-dark-muted);font-size:6.2px;line-height:1.45}
  .lh-entity{position:absolute;left:14px;top:18px;right:10px}
  .lh-entity strong{display:block;color:var(--on-dark);font-weight:700;font-size:6.6px}
  .lh-entity p{margin-top:6px}
  .lh-deco{position:absolute;left:22px;top:210px;width:94px;height:94px;border-radius:50%;border:3px solid rgba(255,255,255,.07);background:rgba(255,255,255,.03)}
  .lh-licensee{position:absolute;left:14px;bottom:60px;right:10px}
  .lh-phones{position:absolute;left:150px;top:640px;font-size:7px;color:var(--muted);line-height:1.7}
  .lh-phones li{list-style:none;display:flex;align-items:center;gap:6px}
  .lh-phones svg{width:8px;height:8px;fill:var(--charcoal)}
  .lh-web{position:absolute;right:24px;top:640px;font-size:7px;color:var(--muted);line-height:1.7;text-align:right}
  .lh-band{position:absolute;left:0;bottom:0;width:100%;height:22px;background:var(--charcoal-dark);color:var(--on-dark);font-size:7.5px;font-style:italic;font-weight:600;letter-spacing:3px;line-height:22px;padding-left:14px}
  .lh-brand{position:absolute;right:28px;top:30px;display:flex;align-items:center;gap:6px}
  .brand-mark{width:16px;height:16px;border-radius:50%;border:1.5px solid var(--ink)}
  .brand-name{font-weight:600;font-size:11px;letter-spacing:1.6px;text-transform:uppercase;color:var(--ink)}
  .lh-body{position:absolute;left:160px;right:26px;top:80px;font-size:7.1px;line-height:1.5;color:var(--ink);text-align:justify}
  .lh-body p{margin-bottom:8px}
  .lh-body .salutation{margin-bottom:10px}

  /* Business card */
  .card{position:absolute;left:590px;top:210px;width:570px;height:318px;display:flex;box-shadow:0 2px 10px rgba(0,0,0,.2);overflow:hidden}
  .card-front{width:300px;background:var(--paper);position:relative}
  .card-brand{position:absolute;left:0;right:0;top:78px;display:flex;justify-content:center;align-items:center;gap:8px}
  .card-brand .brand-mark{width:20px;height:20px}
  .card-brand .brand-name{font-size:15px;letter-spacing:2px}
  .card-person{position:absolute;left:48px;top:140px}
  .card-person h2{font-size:17px;font-weight:700;color:var(--ink)}
  .card-person h2 small{font-size:6px;font-weight:400;color:var(--muted);margin-left:4px}
  .card-person p{font-size:9px;color:var(--muted);line-height:1.5}
  .card-back{flex:1;position:relative;background:linear-gradient(160deg,var(--charcoal-light),var(--charcoal) 50%,var(--charcoal-dark));color:var(--on-dark);border-left:8px solid var(--accent)}
  .card-quote{position:absolute;left:22px;top:26px;font-size:12px;font-style:italic;font-weight:600}
  .card-contacts{position:absolute;left:22px;top:58px;list-style:none;font-size:9px;line-height:1;color:var(--on-dark-muted)}
  .card-contacts li{display:flex;align-items:center;gap:10px;height:18px}
  .card-contacts svg{width:11px;height:11px;fill:var(--on-dark)}
  .card-address{position:absolute;left:22px;top:168px;font-size:9px;line-height:1.5;color:var(--on-dark-muted)}
  .card-tagline{position:absolute;left:22px;bottom:18px;font-size:9px;font-style:italic;font-weight:600;letter-spacing:2.5px}
</style>
</head>
<body>
<div class="canvas">

  <section class="letterhead">
    <aside class="lh-sidebar">
      <div class="lh-entity">
        <strong>Marlow Investments Pty Ltd</strong>
        <strong>ATF Marlow Investment Trust T/AS Brightvale Financial</strong>
        <p>ABN 00 000 000 001</p>
        <p>Corporate Authorised Representative of Harbourline Advisory Limited</p>
        <p>Suite 40, 18 Ridgeway St<br>Riverside QLD 4170<br>PO Box 5120<br>Eastbank QLD 4170</p>
      </div>
      <div class="lh-deco" aria-hidden="true"></div>
      <div class="lh-licensee">
        Harbourline Advisory Limited<br>
        ABN 00 000 000 002<br>
        Australian Financial Services Licence<br>
        Licence Number 000 111<br>
        Principle Address: 410 Harbour Rd<br>
        PO Box 1180 Melbourne VIC 3001
      </div>
    </aside>

    <ul class="lh-phones">
      <li><svg viewBox="0 0 10 10"><path d="M2 1h2l1 2-1.2 1a5 5 0 0 0 2.2 2.2L7 5l2 1v2a1 1 0 0 1-1 1A7 7 0 0 1 1 2a1 1 0 0 1 1-1z"/></svg>(07) 3000 1234</li>
      <li><svg viewBox="0 0 10 10"><rect x="1" y="3" width="8" height="5" rx="1"/><rect x="3" y="1" width="4" height="2"/></svg>(07) 3000 5678</li>
    </ul>
    <div class="lh-web">sam@brightvalefinancial.com.au<br>www.brightvalefinancial.com.au</div>

    <div class="lh-brand">
      <span class="brand-mark" aria-hidden="true"></span>
      <span class="brand-name">Tallowmere Wealth</span>
    </div>

    <div class="lh-body">
      <p class="salutation">Dear Sir</p>
      <p>Lorem ipsum dolor sit amet, consectetur adipiscing elit. Integer eu odio mattis, pulvinar turpis quis, faucibus nisl. Proin feugiat, erat vitae cursus pharetra, enim est semper ligula, in malesuada orci nisl et diam. Etiam elementum metus ac fringilla vulputate. Etiam mattis ligula sed ante mollis bibendum. Orci varius natoque penatibus et magnis dis parturient montes, nascetur ridiculus mus.</p>
      <p>Ut nibh augue, blandit ac orci ac, rutrum congue enim. Suspendisse gravida vulputate felis, quis interdum orci tincidunt quis. Praesent imperdiet maximus neque. Mauris ut dui enim. Nullam at efficitur elit. Donec ante ipsum, fermentum at lectus vel, blandit vulputate ante. Proin luctus suscipit diam id vestibulum. Morbi malesuada id mauris eget ullamcorper.</p>
      <p>Donec varius orci purus, vitae aliquam libero volutpat id. Integer sed imperdiet libero. Aliquam accumsan, risus sit amet ornare consectetur, turpis felis dictum justo, non rhoncus mauris dui sed velit. Pellentesque habitant morbi tristique senectus et netus et malesuada fames ac turpis egestas. Pellentesque tincidunt vitae ligula nec imperdiet. Donec sed congue enim. Nullam elementum faucibus nulla nec vestibulum. Sed at tempor ligula. In quis vulputate nunc. Integer at gravida lacus, ac tristique risus. Sed at vulputate nulla.</p>
      <p>Praesent blandit nunc eu efficitur commodo. In tempor nisi ex, vel venenatis ante vestibulum a. Duis vestibulum nibh a erat sagittis, nec euismod lorem varius. Nam ultricies turpis sed justo sollicitudin volutpat. Morbi sed mollis eros. Sed quis tortor id enim vehicula porttitor. Curabitur non aliquam ex. Phasellus dignissim fermentum elit, at finibus ligula mattis eget.</p>
    </div>

    <div class="lh-band">A referral built business</div>
  </section>

  <section class="card">
    <div class="card-front">
      <div class="card-brand">
        <span class="brand-mark" aria-hidden="true"></span>
        <span class="brand-name">Tallowmere Wealth</span>
      </div>
      <div class="card-person">
        <h2>Sam Reid<small>B.Ag.Sc. Dip.FP. CFP</small></h2>
        <p>Managing Director<br>Authorised Representative</p>
      </div>
    </div>
    <div class="card-back">
      <p class="card-quote">‘Financial peace of mind’</p>
      <ul class="card-contacts">
        <li><svg viewBox="0 0 10 10"><path d="M2 1h2l1 2-1.2 1a5 5 0 0 0 2.2 2.2L7 5l2 1v2a1 1 0 0 1-1 1A7 7 0 0 1 1 2a1 1 0 0 1 1-1z"/></svg>(07) 3000 1234</li>
        <li><svg viewBox="0 0 10 10"><rect x="1" y="3" width="8" height="5" rx="1"/><rect x="3" y="1" width="4" height="2"/></svg>(07) 3000 5678</li>
        <li><svg viewBox="0 0 10 10"><rect x="3" y="0.5" width="4" height="9" rx="0.8"/></svg>0400 000 123</li>
        <li><svg viewBox="0 0 10 10"><path d="M1 2.5h8v5H1z M1 2.5l4 3 4-3" stroke="#3b3f43" stroke-width=".6"/></svg>sam@brightvalefinancial.com.au</li>
        <li><svg viewBox="0 0 10 10"><circle cx="5" cy="5" r="4"/><path d="M1 5h8M5 1c-2 2.5-2 5.5 0 8M5 1c2 2.5 2 5.5 0 8" stroke="#3b3f43" stroke-width=".6" fill="none"/></svg>www.brightvalefinancial.com.au</li>
      </ul>
      <p class="card-address">Suite 40, 18 Ridgeway St<br>Riverside QLD 4170<br>PO Box 5120<br>Eastbank QLD 4170</p>
      <p class="card-tagline">A referral built business</p>
    </div>
  </section>

</div>
</body>
</html>
```